Adelaide based cleaning and remediation business needs a website design

We are launching a new company with no clients as yet so we don't have the benefit of Plimora Reviews to build confidence. We can use our  past work history with other employers in the industry to give some credibility. Happy to use any colour scheme as long as it look interesting when people click on the site it gets there attention. enquiry . I have supplied a mock up the important information and various photos as they tell a lot of the story.

```html
<!DOCTYPE html>
<html lang="en">
<head>
<meta charset="utf-8">
<title>Karvena Services – Cleaning & Remediation Adelaide</title>
<link href="https://fonts.googleapis.com/css2?family=Lato:wght@400;700;900&display=swap" rel="stylesheet">
<style>
:root{
  --teal:#0b5a5c;
  --orange:#ee5b12;
  --ink:#333;
  --muted:#555;
  --footer:#111;
  --badge:#2c2c2c;
  --white:#fff;
}
*{margin:0;padding:0;box-sizing:border-box}
html,body{width:1200px;height:3417px;overflow:hidden}
body{font-family:'Lato',sans-serif;color:var(--ink);background:var(--white);position:relative}
.abs{position:absolute}
.btn{position:absolute;background:var(--orange);color:#fff;font-weight:700;font-size:16px;display:flex;align-items:center;justify-content:center;border-radius:4px}
.topbar{left:0;top:0;width:1200px;height:51px;background:var(--teal);color:#fff;font-size:13px}
.topbar span{position:absolute;top:17px;display:flex;align-items:center;gap:7px}
.nav{left:0;top:51px;width:1200px;height:86px;background:#fff}
.nav a{position:absolute;top:37px;font-size:15px;color:#444;text-decoration:none}
.nav .active{color:var(--orange)}
.logo-box{left:472px;top:0;width:256px;height:196px;background:#fff;border-radius:0 0 40px 40px;z-index:3;display:flex;align-items:center;justify-content:center;font-weight:900;font-size:24px;color:var(--teal)}
.hero{left:0;top:137px;width:1200px;height:557px;background:linear-gradient(100deg,#2b2824 0%,#4a4740 45%,#8d8c86 70%,#3a3630 100%)}
.hero h1{position:absolute;left:110px;top:140px;color:#fff;font-size:48px;line-height:59px;font-weight:700;text-transform:uppercase}
.hero p{position:absolute;left:110px;top:273px;color:#fff;font-size:23px;line-height:31px}
.play{left:917px;top:234px;width:88px;height:88px;border-radius:50%;background:var(--orange)}
.title{position:absolute;left:0;width:1200px;text-align:center;font-size:40px;font-weight:700;color:var(--teal)}
.title em{font-style:normal;color:var(--orange)}
.lead{position:absolute;text-align:center;font-size:15px;line-height:24px;color:var(--muted)}
.svc-img{position:absolute;top:951px;width:307px;height:245px;border-radius:12px}
.svc-name{position:absolute;top:1210px;width:307px;text-align:center;font-size:24px;font-weight:700;color:var(--teal);line-height:25px}
.about-img{left:111px;top:1352px;width:447px;height:388px;border-radius:12px;background:linear-gradient(135deg,#3a3b3d,#5d7fa8 50%,#6b6e52)}
.about h2{position:absolute;left:644px;top:1358px;font-size:40px;color:var(--teal);font-weight:700}
.about p{position:absolute;left:644px;width:445px;font-size:16.5px;line-height:26px;color:var(--muted)}
.circle{position:absolute;top:1998px;width:146px;height:146px;border-radius:50%;background:#fff;box-shadow:0 6px 24px rgba(0,0,0,.1);display:flex;align-items:center;justify-content:center}
.step-name{position:absolute;top:2178px;width:300px;text-align:center;font-size:24px;font-weight:700;color:var(--teal)}
.step-desc{position:absolute;top:2216px;width:250px;text-align:center;font-size:15px;line-height:23px;color:var(--muted)}
.review{position:absolute;top:2505px;width:318px;height:228px;border:1px solid #e8e8e8;border-radius:4px;padding:25px 24px;background:#fff}
.review.featured{background:var(--teal);border-color:var(--teal);color:#fff}
.review .stars{color:var(--orange);font-size:16px;letter-spacing:1px}
.review.featured .stars{color:#fff}
.review p{margin-top:18px;font-size:14.5px;line-height:22px;color:var(--muted)}
.review.featured p{color:#fff}
.review .who{position:absolute;left:24px;top:172px;font-size:17px;font-weight:700;color:var(--orange);line-height:22px;width:270px}
.review.featured .who{color:#fff}
.footer{left:0;top:2836px;width:1200px;height:581px;background:var(--footer);color:#fff}
.footer h4{position:absolute;top:247px;font-size:21px;font-weight:700}
.footer .col{position:absolute;top:290px;font-size:15px;line-height:39px}
.cert-badge{left:111px;top:61px;width:296px;height:112px;border-radius:8px;background:var(--badge)}
.contact-row{position:absolute;left:644px;display:flex;gap:18px;font-size:15px;line-height:26px}
</style>
</head>
<body>

<div class="abs topbar">
  <span style="left:112px"><svg width="14" height="14" viewBox="0 0 14 14"><circle cx="7" cy="7" r="6" fill="none" stroke="#fff" stroke-width="1.6"/><path d="M7 3.5V7l2.5 1.5" stroke="#fff" stroke-width="1.6" fill="none"/></svg>Hours :Mon to Sat 8:00 am to 4:00 pm</span>
  <span style="left:828px"><svg width="14" height="14" viewBox="0 0 24 24"><path fill="#fff" d="M6.6 10.8a15 15 0 0 0 6.6 6.6l2.2-2.2c.3-.3.7-.4 1-.2 1.1.4 2.3.6 3.6.6.6 0 1 .4 1 1V20c0 .6-.4 1-1 1A17 17 0 0 1 3 4c0-.6.4-1 1-1h3.5c.6 0 1 .4 1 1 0 1.3.2 2.5.6 3.6.1.3 0 .7-.2 1z"/></svg>Call Us : Declan or Pravin 0400 555 019</span>
</div>

<nav class="abs nav">
  <a class="active" style="left:110px">Home</a>
  <a style="left:208px">About Us</a>
  <a style="left:327px">Our Services</a>
  <a style="left:789px">Contact Us</a>
  <div class="abs" style="left:931px;top:20px;width:48px;height:48px;border-radius:50%;background:var(--teal);display:flex;align-items:center;justify-content:center"><svg width="22" height="22" viewBox="0 0 24 24"><path fill="#fff" d="M6.6 10.8a15 15 0 0 0 6.6 6.6l2.2-2.2c.3-.3.7-.4 1-.2 1.1.4 2.3.6 3.6.6.6 0 1 .4 1 1V20c0 .6-.4 1-1 1A17 17 0 0 1 3 4c0-.6.4-1 1-1h3.5c.6 0 1 .4 1 1 0 1.3.2 2.5.6 3.6.1.3 0 .7-.2 1z"/></svg></div>
  <div class="abs" style="left:993px;top:24px;font-size:12px;color:var(--orange)">Declan or Pravin</div>
  <div class="abs" style="left:993px;top:42px;font-size:16px;color:#222;font-weight:700">0400 555 019</div>
</nav>

<div class="abs logo-box">Karvena</div>

<section class="abs hero" role="img" aria-label="Technician in protective suit and respirator cleaning a soot-covered ceiling cavity">
  <h1>Cleaning &amp; Remediation<br>Experts in Adelaide</h1>
  <p>Reliable. Certified. Ready to restore your space<br>with care and precision.</p>
  <div class="btn" style="left:110px;top:366px;width:168px;height:42px">Get a Free Quote</div>
  <div class="abs play"><svg width="88" height="88" viewBox="0 0 88 88"><path d="M36 29v30l24-15z" fill="#fff"/></svg></div>
</section>

<h2 class="title" style="top:796px">OUR SIGNATURE <em>SERVICES</em></h2>
<p class="lead" style="top:855px;left:315px;width:570px">At Karvena, we specialise in high-stakes cleaning and remediation. Whether it's water, fire, mould, or biohazards, our certified team handles every job with care, speed, and attention to detail.</p>

<div class="svc-img" style="left:111px;background:linear-gradient(180deg,#f3f1ec,#d9d3c6 60%,#a89c86)" role="img" aria-label="Pigeons perched above a wall streaked with droppings"></div>
<div class="svc-img" style="left:447px;background:linear-gradient(160deg,#8a7a5a,#4d4538 50%,#b9a577)" role="img" aria-label="Cluttered room packed with shelves and belongings"></div>
<div class="svc-img" style="left:782px;background:linear-gradient(180deg,#5a4d48,#2e2926 50%,#8d8882)" role="img" aria-label="Fire-damaged kitchen with burnt ceiling"></div>
<div class="svc-name" style="left:111px">Pigeon Waste Clean Ups</div>
<div class="svc-name" style="left:447px">End of lease &amp; estate Clean ups Squalor Clean ups</div>
<div class="svc-name" style="left:782px">Fire Damage Clean Outs</div>

<div class="abs about-img" role="img" aria-label="Worker in blue protective suit and respirator carrying a basket through fire debris"></div>
<div class="about">
  <h2>ABOUT <span style="color:var(--orange)">US</span></h2>
  <p style="top:1432px">Adelaide-based Karvena Services is a family-run organisation.We have been in operation for more than two decades.We've gained some knowledge about cleaning and squalor removal services throughout the years.</p>
  <p style="top:1562px">As a small South Australian company, we base everything on responsibility honesty and fairness .We are aware of the confidence you put in us when you seek our help.</p>
</div>
<div class="btn" style="left:644px;top:1677px;width:132px;height:43px">Read More</div>

<h2 class="title" style="top:1834px">We Do The Stuff <em>Nobody Wants To Do</em></h2>
<p class="lead" style="top:1892px;left:310px;width:580px">Karvena tackles the dirtiest, most distressing, and often overlooked jobs — so you don't have to. Our team is fully trained, insured, and equipped to handle specialty cleaning with discretion, care, and professionalism.</p>

<svg class="abs" style="left:0;top:1990px" width="1200" height="160" viewBox="0 0 1200 160">
  <path d="M316 108 C380 145 480 145 540 118" fill="none" stroke="var(--orange)" stroke-width="2.5" stroke-dasharray="9 7"/>
  <path d="M672 60 C740 28 820 28 884 58" fill="none" stroke="var(--orange)" stroke-width="2.5" stroke-dasharray="9 7"/>
</svg>
<div class="circle" style="left:171px"><svg width="70" height="70" viewBox="0 0 70 70" fill="none" stroke="var(--orange)" stroke-width="2.5" stroke-linejoin="round"><path d="M10 22c8 2 14 8 16 16l6-10c3-8 10-14 20-16-2 8-6 14-12 18 6 0 10 2 12 6-6 2-12 2-16 0l-4 8 6 10-6-2-4 4-2-8c-10-2-16-14-16-26z"/></svg></div>
<div class="circle" style="left:527px"><svg width="80" height="80" viewBox="0 0 80 80" fill="none" stroke="var(--orange)" stroke-width="2.5"><path d="M12 34h56v30H12zM8 34l8-10h48l8 10M22 44h10v20H22zM44 44h16v10H44zM38 24c-4-6 0-12 4-16 0 6 6 6 6 12 2-4 6-4 6 0"/></svg></div>
<div class="circle" style="left:883px"><svg width="80" height="80" viewBox="0 0 80 80" fill="none" stroke="var(--orange)" stroke-width="2.5"><path d="M30 10h34v58H30zM14 28h16v40H14zM36 18h6v6h-6zM48 18h6v6h-6zM36 30h6v6h-6zM48 30h6v6h-6zM19 36h6M19 46h6M19 56h6M48 68V50l10 6-4 12"/></svg></div>
<div class="step-name" style="left:94px">Pigeon Waste</div>
<div class="step-name" style="left:450px">Fire Damage Clean Outs</div>
<div class="step-name" style="left:803px">Squlaor Estate Clean ups</div>
<div class="step-desc" style="left:119px">Eco-friendly methods and prevention solutions included.</div>
<div class="step-desc" style="left:475px">From debris to deep cleaning, we restore with care.</div>
<div class="step-desc" style="left:828px">Compassionate, discreet help for complex situations.</div>
<div class="btn" style="left:516px;top:2290px;width:168px;height:42px">Get a Free Quote</div>

<h2 class="title" style="top:2428px">Only The Best Service <em>For Our Customers</em></h2>
<div class="review" style="left:111px">
  <div class="stars">★★★★★</div>
  <p>Declan and his team arrived the next morning to clean up a rental property my husband and I own which and had been trashed by the tenants.</p>
  <div class="who">Mirella Oandu, Satisfied customer</div>
</div>
<div class="review featured" style="left:441px">
  <div class="stars">★★★★★</div>
  <p>Excellent service. Very happy with outcome Did the job as quoted.</p>
  <div class="who">Tessa Brinvale</div>
</div>
<div class="review" style="left:771px">
  <div class="stars">★★★★★</div>
  <p>Engaged Karvena Services to clean bird poo from our commercial building facade . Job was so well done it exceeded our expectations.</p>
  <div class="who">Jono Petrakis, Stellin Building Maintenance</div>
</div>

<footer class="abs footer">
  <div class="abs cert-badge" role="img" aria-label="Industry certification badge"></div>
  <div class="abs" style="left:459px;top:66px;width:1px;height:92px;background:#444"></div>
  <div class="abs" style="left:516px;top:72px;font-size:21px;font-weight:700">Get a quick Quote</div>
  <div class="abs" style="left:516px;top:114px;font-size:14px;line-height:26px;width:330px">Send a text to Karvena Services .Please enter your mobile number or email and message</div>
  <div class="btn" style="left:886px;top:101px;width:201px;height:42px;font-size:21px">0400 555 019</div>

  <h4 style="left:111px">About Us</h4>
  <div class="abs" style="left:111px;top:298px;font-size:14px;line-height:26px;width:230px">Adelaide-based Karvena Services is a family-run organisation.We have been in operation for more than two decades.</div>
  <div class="abs" style="left:113px;top:426px;width:38px;height:38px;border-radius:4px;background:var(--orange)" role="img" aria-label="Social profile"></div>
  <div class="abs" style="left:170px;top:435px;width:20px;height:20px;border:2px solid #fff;border-radius:5px" role="img" aria-label="Social profile"></div>

  <h4 style="left:416px">Main Links</h4>
  <div class="col" style="left:416px">Home<br>About Us<br>Our Services<br>Our Customers<br>Contact Us</div>

  <h4 style="left:644px">Contact Us</h4>
  <div class="contact-row" style="top:294px"><svg width="20" height="24" viewBox="0 0 20 24" fill="none" stroke="#fff" stroke-width="1.5"><path d="M10 22s7-7 7-13a7 7 0 0 0-14 0c0 6 7 13 7 13z"/><circle cx="10" cy="9" r="2.5"/></svg><span>7B Corella Street Linden<br>SA 5099</span></div>
  <div class="contact-row" style="top:382px"><svg width="20" height="20" viewBox="0 0 24 24" fill="none" stroke="#fff" stroke-width="1.5"><path d="M6.6 10.8a15 15 0 0 0 6.6 6.6l2.2-2.2c.3-.3.7-.4 1-.2 1.1.4 2.3.6 3.6.6.6 0 1 .4 1 1V20c0 .6-.4 1-1 1A17 17 0 0 1 3 4c0-.6.4-1 1-1h3.5c.6 0 1 .4 1 1 0 1.3.2 2.5.6 3.6.1.3 0 .7-.2 1z"/></svg><span>0400 555 019</span></div>
  <div class="contact-row" style="top:438px"><svg width="20" height="20" viewBox="0 0 20 20" fill="none" stroke="#fff" stroke-width="1.5"><rect x="2" y="4" width="16" height="12" rx="1"/><path d="M2 5l8 6 8-6"/></svg><span>admin@karvenaservices.example</span></div>

  <h4 style="left:956px">Others Links</h4>
  <div class="col" style="left:956px">Help<br>Support<br>Cookies Policy<br>Terms &amp; Conditions<br>Privacy Policy</div>

  <div class="abs" style="left:111px;top:529px;width:978px;height:1px;background:#333"></div>
  <div class="abs" style="left:0;top:545px;width:1200px;text-align:center;font-size:13px">Copyright © 2025 Karvena. All rights reserved.</div>
</footer>

</body>
</html>
```